Web design for Crowdfunding site HopeWingsRally.com

We need a web design for christian crowdfunding website. Here is the challenge: We need responsive layout that is targeted first in iPad size of screen. It should also scale somehow down to iPhone size of screens. Web layout can be about the same size as iPad screen.

Screens should work so that main page scrolls not but only certain part of the screen scrolls and always one "page" at time. We can implement these "scrolls" then later with javascript but now we need only design. The challenge is to create this kind of hybrid website / app look.

Target is at first to raise funds to orphan people needing about $40 per month for their living and education. There is always some organization which takes care of these kids. Later there will be other christian missions included. At first we are looking to find monthly supporters.

You can be as creative as you want :) As you see from the look and feel sector, I am not looking any same traditional look which many "help kids" sites have. I am looking to reach now younger generation and therefore iPad and mobile are the main screen sizes.

Inspirational designs:
- https://example-gallery.test/profiles/studiofernlake/designs/482716?from=%2Fbrowse%2Fxhr%2Fdesigns%3Fcategory%3Dmobile-app-design
- http://www.artpoolhub.test/design/8261047 Clear, simple visuals
- http://www.artpoolhub.test/design/7394215 Header
- http://www.artpoolhub.test/design/6048392 Contrast in the colors, i think is powerfull

Some terms could be: Kids play, kids are learning (in the school). No static posture but living like kids are. I wonder also how we could also add little bit gaming style even though the question is of reali life of real people. Giving should be rewarding.

Target Market(s)

People who want help other people.

Industry/Entity Type

Christian

Number of Pages Required

4 page

Requirements
Must have
• Homepage. Mission page (In my wireframes it was one kid).
Nice to have
• Other pages and some idea how to scroll. 4 pages is no must. If you feel easy, please give first some draft and I give comments on that.

```html
<!DOCTYPE html>
<html lang="en">
<head>
<meta charset="utf-8">
<title>HopeWingsRally – My Missions</title>
<link href="https://fonts.googleapis.com/css2?family=Montserrat:wght@400;500;600;700&family=Open+Sans:wght@400;600&display=swap" rel="stylesheet">
<style>
  :root {
    --teal: #4fcbb0;
    --teal-light: #8fe0cc;
    --teal-dark: #2fae93;
    --green: #3ccf6a;
    --blue: #2f7de1;
    --page: #f0eff5;
    --card: #ffffff;
    --ink: #2b2b2b;
    --muted: #8b8b93;
    --line: #dcdbe3;
    --backdrop: #f2f1ec;
  }
  * { box-sizing: border-box; margin: 0; padding: 0; }
  html, body { width: 1200px; height: 800px; overflow: hidden; }
  body {
    background: var(--backdrop);
    font-family: "Open Sans", Arial, sans-serif;
    color: var(--ink);
    display: flex; align-items: center; justify-content: center;
  }
  .screen {
    width: 600px; height: 770px; background: var(--page);
    display: flex; flex-direction: column; overflow: hidden;
    box-shadow: 0 2px 14px rgba(0,0,0,.08);
  }
  /* header */
  .topbar {
    height: 50px; background: linear-gradient(90deg, var(--teal), var(--teal-light));
    display: flex; align-items: center; justify-content: space-between; padding: 0 18px;
    font-family: "Montserrat", Arial, sans-serif; color: #fff;
  }
  .menu { display: flex; align-items: center; gap: 8px; font-size: 10px; font-weight: 600; letter-spacing: .3px; }
  .menu svg { display: block; }
  .brand { font-size: 15px; font-weight: 600; letter-spacing: .6px; color: #1f5f52; }
  .auth { display: flex; gap: 14px; font-size: 9.5px; font-weight: 500; }
  /* hero */
  .hero {
    position: relative; height: 282px;
    background: linear-gradient(135deg, #f4f4f2 0%, #c9c8c4 45%, #8a8985 75%, #e6e5e1 100%);
  }
  .hero-note {
    position: absolute; left: 130px; top: 12px; width: 150px;
    font-size: 6.5px; line-height: 1.35; color: #333;
  }
  .hero-band { height: 18px; background: var(--teal); }
  /* content */
  .content { flex: 1; padding: 12px 22px 0; display: flex; flex-direction: column; gap: 10px; position: relative; }
  .profile-row { display: flex; justify-content: space-between; }
  .profile { display: flex; align-items: center; gap: 14px; }
  .avatar-lg {
    width: 62px; height: 62px; border-radius: 50%; border: 2px solid #9b9ba3;
    background: #fff; display: flex; align-items: flex-end; justify-content: center; overflow: hidden;
  }
  .identity { font-size: 9px; line-height: 1.6; }
  .following { font-size: 8px; }
  .section-title {
    font-family: "Montserrat", Arial, sans-serif; font-size: 8.5px; font-weight: 600;
    letter-spacing: .4px; text-transform: uppercase; margin-bottom: 4px;
  }
  .following li { list-style: none; display: flex; align-items: center; gap: 6px; margin-top: 3px; color: var(--muted); }
  .avatar-sm { width: 16px; height: 16px; border-radius: 50%; background: #c7c6cc; flex: none; }
  .avatar-md { width: 28px; height: 28px; border-radius: 50%; background: #c7c6cc; border: 2px solid #e4e3e8; flex: none; }
  .missions { display: grid; grid-template-columns: 1fr 1fr; gap: 18px; }
  .mission-list { display: flex; flex-direction: column; gap: 5px; }
  .mission-card {
    background: var(--card); border-radius: 3px; padding: 7px 9px;
    display: flex; align-items: center; gap: 8px; box-shadow: 0 1px 2px rgba(0,0,0,.05);
  }
  .kid { flex: 1; font-size: 8.5px; line-height: 1.3; }
  .kid b { font-weight: 600; }
  .dot { width: 5px; height: 5px; border-radius: 50%; background: var(--blue); flex: none; }
  .stats { font-size: 6.5px; line-height: 1.45; color: var(--muted); }
  .ring { position: relative; width: 28px; height: 28px; flex: none; }
  .ring span { position: absolute; inset: 0; display: flex; align-items: center; justify-content: center; font-size: 7px; color: var(--muted); }
  .plus { flex: none; }
  .swipe { display: flex; justify-content: space-between; font-size: 7.5px; color: var(--muted); padding: 4px 4px 0; }
  .activities { display: grid; grid-template-columns: 1fr 1fr; gap: 18px; }
  .activity-col { display: flex; flex-direction: column; gap: 5px; }
  .activity {
    background: var(--card); border-radius: 3px; padding: 7px 9px; display: flex; gap: 7px;
    font-size: 7.5px; line-height: 1.35;
  }
  .activity .dot { margin-top: 3px; }
  .activity-body { flex: 1; }
  .activity-head { display: flex; justify-content: space-between; }
  .activity-head b { font-weight: 600; font-size: 8.5px; }
  .time { color: var(--muted); font-size: 6.5px; }
  .activity p { color: var(--muted); }
  .next-page {
    position: absolute; right: 20px; bottom: 8px; font-family: "Montserrat", Arial, sans-serif;
    font-size: 8.5px; font-weight: 600; display: flex; align-items: center; gap: 4px;
  }
</style>
</head>
<body>
<main class="screen">
  <header class="topbar">
    <div class="menu">
      <svg width="13" height="10" viewBox="0 0 13 10"><rect width="13" height="2" fill="#1f3d37"/><rect y="4" width="13" height="2" fill="#1f3d37"/><rect y="8" width="13" height="2" fill="#1f3d37"/></svg>
      SEE THE MISSIONS
    </div>
    <div class="brand">HOPEWINGSRALLY</div>
    <nav class="auth"><span>LOG IN</span><span>SIGN UP</span></nav>
  </header>

  <section class="hero" role="img" aria-label="Black and white photo of two smiling children, the younger one eating an orange">
    <p class="hero-note">Every child deserves a chance to learn, play and grow. Join a mission today and give hope monthly.</p>
  </section>
  <div class="hero-band"></div>

  <section class="content">
    <div class="profile-row">
      <div class="profile">
        <div class="avatar-lg">
          <svg width="40" height="46" viewBox="0 0 40 46"><circle cx="20" cy="15" r="10" fill="#9b9ba3"/><path d="M2 46 C4 30 36 30 38 46Z" fill="#9b9ba3"/></svg>
        </div>
        <div class="identity">
          <div>Name: MATTHEW MATT</div>
          <div>Username: matt28</div>
        </div>
      </div>
      <div class="following">
        <div class="section-title">Following</div>
        <ul>
          <li><span class="avatar-sm"></span>Maria,...</li>
          <li><span class="avatar-sm"></span>Maria,...</li>
          <li><span class="avatar-sm"></span>Maria,...</li>
        </ul>
      </div>
    </div>

    <div class="missions">
      <div>
        <div class="section-title">My Missions ⌄</div>
        <div class="mission-list">
          <article class="mission-card">
            <span class="avatar-md"></span>
            <div class="kid"><b>Maria, 11y</b><br>Orphan, Jacob</div>
            <span class="dot"></span>
            <div class="stats">$15 raised<br>$20 to go<br>5 angels in</div>
            <div class="ring"><svg width="28" height="28" viewBox="0 0 28 28"><circle cx="14" cy="14" r="11" fill="none" stroke="#e2e1e7" stroke-width="3"/><circle cx="14" cy="14" r="11" fill="none" stroke="#4fcbb0" stroke-width="3" stroke-dasharray="31 69" transform="rotate(-90 14 14)"/></svg><span>45</span></div>
            <svg class="plus" width="12" height="12" viewBox="0 0 12 12"><circle cx="6" cy="6" r="6" fill="#3ccf6a"/><path d="M6 3v6M3 6h6" stroke="#fff" stroke-width="1.6"/></svg>
          </article>
          <article class="mission-card">
            <span class="avatar-md"></span>
            <div class="kid"><b>Matthew, 11y</b><br>Orphan, Jacob</div>
            <div class="stats">$15 raised<br>$20 to go<br>5 angels in</div>
            <div class="ring"><svg width="28" height="28" viewBox="0 0 28 28"><circle cx="14" cy="14" r="11" fill="none" stroke="#e2e1e7" stroke-width="3"/><circle cx="14" cy="14" r="11" fill="none" stroke="#4fcbb0" stroke-width="3" stroke-dasharray="31 69" transform="rotate(-90 14 14)"/></svg><span>45</span></div>
            <svg class="plus" width="12" height="12" viewBox="0 0 12 12"><circle cx="6" cy="6" r="6" fill="#3ccf6a"/><path d="M6 3v6M3 6h6" stroke="#fff" stroke-width="1.6"/></svg>
          </article>
          <article class="mission-card">
            <span class="avatar-md"></span>
            <div class="kid"><b>Maria, 11y</b><br>Orphan, Jacob</div>
            <span class="dot"></span>
            <div class="stats">$15 raised<br>$20 to go<br>5 angels in</div>
            <div class="ring"><svg width="28" height="28" viewBox="0 0 28 28"><circle cx="14" cy="14" r="11" fill="none" stroke="#e2e1e7" stroke-width="3"/><circle cx="14" cy="14" r="11" fill="none" stroke="#4fcbb0" stroke-width="3" stroke-dasharray="31 69" transform="rotate(-90 14 14)"/></svg><span>45</span></div>
            <svg class="plus" width="12" height="12" viewBox="0 0 12 12"><circle cx="6" cy="6" r="6" fill="#3ccf6a"/><path d="M6 3v6M3 6h6" stroke="#fff" stroke-width="1.6"/></svg>
          </article>
        </div>
      </div>
      <div>
        <div class="section-title">&nbsp;</div>
        <div class="mission-list">
          <article class="mission-card">
            <span class="avatar-md"></span>
            <div class="kid"><b>Maria, 11y</b><br>Orphan, Jacob</div>
            <div class="stats">$15 raised<br>$20 to go<br>5 angels in</div>
            <div class="ring"><svg width="28" height="28" viewBox="0 0 28 28"><circle cx="14" cy="14" r="11" fill="none" stroke="#e2e1e7" stroke-width="3"/><circle cx="14" cy="14" r="11" fill="none" stroke="#4fcbb0" stroke-width="3" stroke-dasharray="31 69" transform="rotate(-90 14 14)"/></svg><span>45</span></div>
            <svg class="plus" width="12" height="12" viewBox="0 0 12 12"><circle cx="6" cy="6" r="6" fill="#3ccf6a"/><path d="M6 3v6M3 6h6" stroke="#fff" stroke-width="1.6"/></svg>
          </article>
          <article class="mission-card">
            <span class="avatar-md"></span>
            <div class="kid"><b>Matthew, 11y</b><br>Orphan, Jacob</div>
            <div class="stats">$15 raised<br>$20 to go<br>5 angels in</div>
            <div class="ring"><svg width="28" height="28" viewBox="0 0 28 28"><circle cx="14" cy="14" r="11" fill="none" stroke="#e2e1e7" stroke-width="3"/><circle cx="14" cy="14" r="11" fill="none" stroke="#4fcbb0" stroke-width="3" stroke-dasharray="31 69" transform="rotate(-90 14 14)"/></svg><span>45</span></div>
            <svg class="plus" width="12" height="12" viewBox="0 0 12 12"><circle cx="6" cy="6" r="6" fill="#3ccf6a"/><path d="M6 3v6M3 6h6" stroke="#fff" stroke-width="1.6"/></svg>
          </article>
          <div class="swipe"><span>• • •</span><span>Swipe to &nbsp; see more?</span></div>
        </div>
      </div>
    </div>

    <div class="activities">
      <div>
        <div class="section-title">Activities ›</div>
        <div class="activity-col">
          <article class="activity">
            <span class="dot"></span>
            <div class="activity-body">
              <div class="activity-head"><b>Maria<br>Report</b><span class="time">10:51 AM ›</span></div>
              <p>Half year report...</p>
            </div>
          </article>
          <article class="activity">
            <span class="dot"></span>
            <div class="activity-body">
              <div class="activity-head"><b>Imma Mustard</b><span class="time">10:51 AM ›</span></div>
              <p>This is and important message. Lorem ipsum dolor sit amet, sapien etiam, nunc amet dolor ac odio mauris justo.</p>
            </div>
          </article>
        </div>
      </div>
      <div>
        <div class="section-title">&nbsp;</div>
        <div class="activity-col">
          <article class="activity">
            <span class="dot"></span>
            <div class="activity-body">
              <div class="activity-head"><b>Maria<br>Got a new angel</b><span class="time">10:51 AM ›</span></div>
              <p>Anonymous</p>
            </div>
          </article>
          <article class="activity">
            <span class="dot"></span>
            <div class="activity-body">
              <div class="activity-head"><b>Matthew<br>Prayer request</b><span class="time">10:51 AM ›</span></div>
              <p>Lorem ipsum dolor sit amet, sapien etiam, nunc amet dolor ac odio mauris justo.</p>
            </div>
          </article>
        </div>
      </div>
    </div>

    <div class="next-page">NEXT PAGE
      <svg width="10" height="8" viewBox="0 0 10 8"><path d="M1 1l3 3-3 3M5 1l3 3-3 3" fill="none" stroke="#2f7de1" stroke-width="1.3"/></svg>
    </div>
  </section>
</main>
</body>
</html>
```